Stationery Set for Velmora Company

I need to create full stationery design for my company; Business Cards, Envelops, Letter Heads, Calendar.
In the letter head and Envelops... only contact information and website links.
Our company is a Service Management company with different domains of innovative services including Technology Service Management, Education Services, Outsourcing Management, Events Management.
I need a modern and innovative design specially for the business card. I some transparent designs and I like it, but don't limit your innovation to what I mentioned. Sky is limit for your innovation.

Target Market(s)

Middle East & Africa

Industry/Entity Type

Business Management

Colors
34a7d8
0355a3
85acd3
86cae7
cee9f5
cfdeed
e4daeb
f3f1f8
ecf7fb

Requirements
Must have
• Name, Title, Email, Mobile
Nice to have
• We have multiple locations in USA, KSA, EGY, so I need ideas about how to include all contact details maybe QR / Barcode or something else.
• Please see our locations and contact information: www.brightvelmora.example
Should not have
• Too much text

```html
<!DOCTYPE html>
<html lang="en">
<head>
<meta charset="utf-8">
<title>Velmora Company – Business Card</title>
<link href="https://fonts.googleapis.com/css2?family=Arimo:wght@400;700&display=swap" rel="stylesheet">
<style>
  :root {
    --page-bg: #e9e9eb;
    --card-white: #ffffff;
    --panel-grey: #d3cecc;
    --brand-blue: #3d6db5;
    --ink: #1e1e1e;
    --muted: #555555;
  }
  * { box-sizing: border-box; margin: 0; padding: 0; }
  html, body { width: 1200px; height: 750px; overflow: hidden; }
  body {
    background: var(--page-bg);
    font-family: "Arimo", Arial, sans-serif;
    position: relative;
  }
  .card {
    position: absolute;
    top: 220px;
    width: 540px;
    height: 309px;
    background: var(--card-white);
    box-shadow: 0 6px 18px rgba(0,0,0,0.18);
  }
  .card--front { left: 40px; display: flex; align-items: center; justify-content: center; }
  .card--back { left: 620px; background: var(--panel-grey); }

  .wordmark {
    display: flex; align-items: center; gap: 10px;
    color: var(--brand-blue);
    font-weight: 700;
    font-size: 34px;
    letter-spacing: 0.5px;
  }
  .wordmark__dot {
    width: 14px; height: 14px; border-radius: 50%;
    background: var(--brand-blue);
  }
  .wordmark--small { font-size: 24px; gap: 8px; }
  .wordmark--small .wordmark__dot { width: 10px; height: 10px; }

  .contact-panel {
    position: absolute; left: 22px; top: 40px; width: 220px;
    font-size: 13px; line-height: 16px; color: var(--ink);
  }
  .contact-block { margin-bottom: 6px; }
  .contact-line { display: flex; align-items: center; gap: 7px; }
  .contact-line svg { flex: 0 0 auto; fill: var(--brand-blue); }

  .identity-box {
    position: absolute; right: 18px; top: 18px;
    width: 272px; height: 273px;
    background: var(--card-white);
    border: 3px solid var(--brand-blue);
    display: flex; flex-direction: column; align-items: center; justify-content: center;
  }
  .person-name {
    margin-top: 18px;
    color: var(--brand-blue);
    font-weight: 700;
    font-size: 19px;
    letter-spacing: 0.5px;
  }
  .person-title { color: var(--muted); font-size: 14px; margin-top: 3px; }
</style>
</head>
<body>
  <section class="card card--front">
    <div class="wordmark"><span class="wordmark__dot"></span>Velmora Company</div>
  </section>

  <section class="card card--back">
    <div class="contact-panel">
      <div class="contact-block">
        <p>418 Harbor Crest Avenue</p>
        <p>5th Floor Lakeview City</p>
        <p>CA 94012 US</p>
        <p class="contact-line">
          <svg width="12" height="12" viewBox="0 0 24 24"><path d="M6.6 10.8a15 15 0 0 0 6.6 6.6l2.2-2.2a1 1 0 0 1 1-.25 11.4 11.4 0 0 0 3.6.57 1 1 0 0 1 1 1V20a1 1 0 0 1-1 1A17 17 0 0 1 3 4a1 1 0 0 1 1-1h3.5a1 1 0 0 1 1 1c0 1.25.2 2.45.57 3.6a1 1 0 0 1-.25 1z"/></svg>
          +1.5550148832</p>
      </div>
      <div class="contact-block">
        <p>Riyadh, Al Nakheel,</p>
        <p>Hassan Al Qamar St.</p>
        <p>Almanar Plaza Buildings</p>
        <p>Block 4C 3rd Floor B12, B18</p>
        <p class="contact-line">
          <svg width="12" height="12" viewBox="0 0 24 24"><path d="M6.6 10.8a15 15 0 0 0 6.6 6.6l2.2-2.2a1 1 0 0 1 1-.25 11.4 11.4 0 0 0 3.6.57 1 1 0 0 1 1 1V20a1 1 0 0 1-1 1A17 17 0 0 1 3 4a1 1 0 0 1 1-1h3.5a1 1 0 0 1 1 1c0 1.25.2 2.45.57 3.6a1 1 0 0 1-.25 1z"/></svg>
          +966 55 010 2217</p>
      </div>
      <p class="contact-line">
        <svg width="12" height="14" viewBox="0 0 12 18"><path d="M2 0h8a2 2 0 0 1 2 2v14a2 2 0 0 1-2 2H2a2 2 0 0 1-2-2V2a2 2 0 0 1 2-2zm0 2v11h8V2zm4 12.5a1 1 0 1 0 0 2 1 1 0 0 0 0-2z"/></svg>
        +1.5550148832</p>
      <p class="contact-line">
        <svg width="12" height="10" viewBox="0 0 24 18"><path d="M0 0h24v18H0zm2 2v.5l10 7 10-7V2zm0 3v11h20V5l-10 7z"/></svg>
        info@brightvelmora.example</p>
    </div>

    <div class="identity-box">
      <div class="wordmark wordmark--small"><span class="wordmark__dot"></span>Velmora Company</div>
      <p class="person-name">RAMI HADDAD</p>
      <p class="person-title">President</p>
    </div>
  </section>
</body>
</html>
```